Wordpress website design for a high-end painting business

We are currently rebranding and are looking to update our Wordpress theme. We have recently rebranded our logo on PixelHarbor, and would like our website to be equally as refined.
Our business is named “Fenwick Painters”. We are a high-end painting business that is known for being professional and having high standards. Our clean and professional image is important as it separates us from our competition. Our current website can be found at www.fenwickcoatings.co.nz . We designed the site ourselves so it is understandably rudimentary. We are generally happy with the. page layout of our existing site, but we like a professional remodel. Any ideas on improvement welcomed.
We would like the front page of the website to summarise all of the info throughout the whole website (I.e introduction, photos, testimonials, contact info etc.) as visitors typically scroll through the first page to see that we are reputable and get to our contact number/email contact at the bottom of the page. We would like this first page to give a clean well rounded image of our business. We would like the gallery to be a scroll through of large photos, as it is difficult to see paint details in smaller photos. A contact page with an enquiry section would also be good.
For the colour scheme, we would like something that fits a bold, masculine and high end theme (similar to our logo attached).
We would like the footer to include Velmora paint logos and the accredited painter logo we have included as these are important to our profession.
We have attached some photos of our work also. I will add more in the coming days. More can also be found on our website.
If you have questions or comments, please don’t hesitate to ask and I will get back as soon as possible.
We are open to your own interpretation or ideas for a better layout/site provided they fit the general brief of being a well rounded site for our profession.
Thanks,
Fenwick Painters.
Target Market(s)
High end clients
Industry/Entity Type
Painting (interior and exterior)
Coding
Coded - Design and coding required
Requirements
Must have
- Classy feel, separating us from typical painting companies. Well rounded homepage.
Nice to have
- Lots of examples of our work
Should not have
- Untidy paint motifs (eg, paint droplets, paint splashes)

```html
<!DOCTYPE html>
<html lang="en">
<head>
<meta charset="utf-8">
<title>Fenwick Painters</title>
<link href="https://fonts.googleapis.com/css2?family=Playfair+Display:wght@700;900&family=Roboto:wght@400;500&display=swap" rel="stylesheet">
<style>
:root{
  --brown:#86653a;
  --brown-dark:#6f5230;
  --navy:#151b29;
  --ink:#222;
  --body:#3a3a3a;
  --white:#fff;
  --gold:#f2b51c;
}
*{box-sizing:border-box;margin:0;padding:0}
html,body{width:1200px;height:3614px;overflow:hidden}
body{position:relative;font-family:"Roboto",Arial,sans-serif;color:var(--body);background:var(--white)}
.abs{position:absolute}
.serif{font-family:"Playfair Display",Georgia,serif;font-weight:700;text-transform:uppercase}

/* nav */
.site-nav{left:0;top:0;width:1200px;height:71px;background:var(--white);z-index:5}
.brand-badge{left:140px;top:-26px;width:112px;height:112px;border-radius:50%;background:var(--white);box-shadow:0 2px 6px rgba(0,0,0,.15);display:flex;align-items:flex-end;justify-content:center;padding-bottom:16px;z-index:6}
.brand-name{font-family:"Playfair Display",Georgia,serif;font-weight:700;font-size:14px;color:var(--navy);text-align:center;line-height:1.05;letter-spacing:.5px}
.nav-menu{left:283px;top:24px;display:flex;gap:30px;list-style:none}
.nav-menu li{font-family:"Playfair Display",Georgia,serif;font-size:15px;color:#333;text-transform:uppercase;position:relative}
.nav-menu li.active::after{content:"";position:absolute;left:50%;bottom:-10px;width:34px;height:3px;background:var(--brown);transform:translateX(-50%)}
.nav-search{left:913px;top:18px;width:32px;height:32px;border-radius:50%;background:#e8e8e8;display:flex;align-items:center;justify-content:center}
.nav-login{left:980px;top:14px;width:109px;height:40px;border-radius:20px;background:var(--brown);color:var(--white);font-family:"Playfair Display",Georgia,serif;font-weight:700;font-size:15px;display:flex;align-items:center;justify-content:space-between;padding:0 4px 0 14px}
.nav-login .dot{width:32px;height:32px;border-radius:50%;background:var(--white);display:flex;align-items:center;justify-content:center}

/* hero */
.hero{left:0;top:71px;width:1200px;height:680px;overflow:hidden}
.hero-photo{position:absolute;inset:0;background:linear-gradient(180deg,#8d949a 0%,#b9b49c 35%,#6f7a55 65%,#4c6a2e 100%)}
.hero-shade{position:absolute;inset:0;background:rgba(20,20,20,.25)}
.hero-curve{position:absolute;left:0;top:0}
.hero-kicker{left:0;width:1200px;top:172px;text-align:center;color:var(--white);font-size:40px}
.hero-title{left:0;width:1200px;top:228px;text-align:center;color:var(--white);font-size:62px}
.btn{display:flex;align-items:center;justify-content:space-between;border-radius:24px;color:var(--white);font-family:"Playfair Display",Georgia,serif;font-weight:700;font-size:15px;text-transform:uppercase;padding:0 5px 0 16px;height:48px}
.btn .arrow{width:38px;height:38px;border-radius:50%;background:var(--white);display:flex;align-items:center;justify-content:center}
.btn-brown{background:var(--brown)}
.btn-dark{background:var(--navy)}
.hero-btn{left:513px;top:403px;width:174px}
.slider-dashes{left:540px;top:555px;display:flex;gap:12px}
.slider-dashes span{width:32px;height:5px;border-radius:3px;background:rgba(30,30,30,.7)}
.slider-dashes span.on{background:var(--white)}

/* about */
.about{left:0;top:730px;width:1200px;height:558px;background:linear-gradient(180deg,#ffffff 0%,#eef0f3 50%,#f5f6f8 100%)}
.about h2{position:absolute;left:112px;top:80px;font-size:33px;color:var(--ink)}
.about-copy{position:absolute;left:112px;top:137px;width:443px;font-size:14px;line-height:25.8px;color:#333}
.about-copy p+p{margin-top:13px}
.about-btn{left:112px;top:424px;width:174px}
.about-mark{left:624px;top:118px;width:324px;height:324px;border-radius:50%;background:radial-gradient(circle,#2a3140 0%,#151b29 75%);display:flex;align-items:center;justify-content:center;color:#c7a46a;font-family:"Playfair Display",Georgia,serif;font-weight:700;font-size:30px;text-align:center;line-height:1.2}

/* services */
.services{left:0;top:1288px;width:1200px;height:558px;background:linear-gradient(180deg,#8b6b3f,#7f6037)}
.section-title{position:absolute;left:0;width:1200px;text-align:center;font-size:34px}
.services .section-title{top:56px;color:var(--white)}
.service-list{position:absolute;left:125px;top:153px;display:flex;gap:54px;list-style:none}
.service-item{width:196px;text-align:center}
.service-photo{width:196px;height:196px;border-radius:50%;border:5px solid #1a2030}
.service-item h3{margin-top:28px;color:var(--white);font-size:15px;white-space:nowrap}
.services-btn{left:513px;top:447px;width:174px}

/* gallery */
.gallery{left:0;top:1846px;width:1200px;height:687px;background:var(--white)}
.gallery .section-title{top:76px;color:var(--ink)}
.g{position:absolute}
.gallery-arrow{position:absolute;top:368px}

/* testimonials */
.testimonials{left:0;top:2533px;width:1200px;height:1081px;background:linear-gradient(180deg,#86683f,#7a5c35)}
.testimonials .section-title{top:62px;color:var(--white)}
.quote-card{position:absolute;top:134px;width:315px;height:230px;background:var(--white);border-radius:14px;padding:14px 18px;text-align:center}
.quote-mark{font-family:"Playfair Display",Georgia,serif;font-weight:900;font-size:44px;line-height:36px;color:var(--brown);height:32px}
.quote-card p{margin-top:8px;font-size:13px;line-height:23px;color:#444}
.author{position:absolute;top:378px;display:flex;align-items:center;gap:18px}
.avatar{width:70px;height:70px;border-radius:50%;border:3px solid var(--white);background:linear-gradient(160deg,#7d8795,#3d4656)}
.author h4{font-size:13px;color:var(--white)}
.stars{color:var(--gold);font-size:15px;letter-spacing:3px;margin-top:3px}
.dots{position:absolute;left:571px;top:491px;display:flex;gap:10px}
.dots span{width:12px;height:12px;border-radius:50%;background:var(--white)}
.dots span.on{background:var(--navy)}

/* footer */
.footer-shape{left:0;top:3100px}
.footer-col{position:absolute;top:3284px;color:var(--white)}
.footer-col h5{font-family:"Playfair Display",Georgia,serif;font-weight:700;font-size:14px;text-transform:uppercase;margin-bottom:18px}
.footer-col ul{list-style:none}
.footer-col li{font-size:15px;line-height:39px}
.footer-col p{font-size:15px;line-height:23px}
.mail-form{display:flex;gap:8px;margin-top:17px}
.mail-input{width:231px;height:36px;background:var(--white);font-size:12px;color:#888;padding:11px 20px}
.mail-btn{width:40px;height:36px;background:var(--brown);display:flex;align-items:center;justify-content:center}
.privacy{margin-top:14px}
.socials{display:flex;gap:7px;margin-top:20px}
.socials span{width:40px;height:36px;background:#262d3b}
.socials span.on{background:var(--brown)}
.contact-row{display:flex;align-items:center;gap:14px;font-size:15px;padding:10px 0;border-bottom:1px solid #5c6270;width:236px;white-space:nowrap}
.contact-row:last-child{border-bottom:0}
.footer-rule{left:112px;top:3548px;width:978px;height:1px;background:#5c6270}
.partners{left:112px;top:3562px;display:flex;align-items:center;gap:10px}
.partner-name{display:flex;align-items:center;gap:6px;color:var(--white);font-family:"Roboto",Arial,sans-serif;font-weight:500;font-size:17px}
.partner-name i{width:14px;height:14px;background:var(--white);display:block}
.partner-badge{width:160px;height:30px;background:#3a6fb5}
.copyright{right:110px;top:3572px;color:var(--white);font-size:14px}
</style>
</head>
<body>

<header class="abs site-nav">
  <div class="abs brand-badge"><div class="brand-name">FENWICK<br>PAINTERS</div></div>
  <ul class="abs nav-menu">
    <li class="active">Home</li><li>Services</li><li>Gallery</li><li>About</li><li>Contact</li><li>All Testimonials</li>
  </ul>
  <div class="abs nav-search"><svg width="14" height="14" viewBox="0 0 14 14"><circle cx="6" cy="6" r="4.3" fill="none" stroke="#222" stroke-width="2"/><line x1="9" y1="9" x2="13" y2="13" stroke="#222" stroke-width="2.2"/></svg></div>
  <div class="abs nav-login">LOGIN<span class="dot"><svg width="12" height="14" viewBox="0 0 12 14"><path d="M3 6V4a3 3 0 0 1 6 0v2" fill="none" stroke="#86653a" stroke-width="1.8"/><rect x="1" y="6" width="10" height="8" rx="1" fill="#86653a"/></svg></span></div>
</header>

<section class="abs hero">
  <div class="hero-photo" role="img" aria-label="Freshly painted cream house with a corrugated roof, lawn and painter at work"></div>
  <div class="hero-shade"></div>
  <svg class="hero-curve" width="1200" height="680" viewBox="0 0 1200 680">
    <path d="M0 455 Q600 800 1200 455 L1200 680 L0 680 Z" fill="#86653a"/>
    <path d="M0 475 Q600 815 1200 475 L1200 680 L0 680 Z" fill="#ffffff"/>
  </svg>
  <div class="abs serif hero-kicker">Welcome to</div>
  <h1 class="abs serif hero-title">Fenwick Painter</h1>
  <div class="abs btn btn-brown hero-btn">Get Started<span class="arrow"><svg width="16" height="16" viewBox="0 0 16 16"><circle cx="8" cy="8" r="8" fill="#222"/><path d="M4 8h7M8 5l3 3-3 3" stroke="#fff" stroke-width="1.8" fill="none"/></svg></span></div>
  <div class="abs slider-dashes"><span></span><span class="on"></span><span></span></div>
</section>

<section class="abs about">
  <h2 class="serif">About Us</h2>
  <div class="about-copy">
    <p>Here at Fenwick Painters, we take a lot of pride in our work.We strive to ensure the highest quality paint-work paying close attention detail to provide a long lasting finish. Our clients are always our priority, we aim to deliver beyond their expectations. It is our goal to provide an excellent service from start to finish through clear communication, free quoting and transparency with our pricing.</p>
    <p>We take great pride in the preparation of surfaces for painting and only use the best quality products ensure we achieve the best finish for you.Our qualified interior designer can also assist you with your colour selection as a part of our free colour consultancy service.</p>
  </div>
  <div class="abs btn btn-brown about-btn">Learn More<span class="arrow"><svg width="16" height="16" viewBox="0 0 16 16"><circle cx="8" cy="8" r="8" fill="#222"/><path d="M4 8h7M8 5l3 3-3 3" stroke="#fff" stroke-width="1.8" fill="none"/></svg></span></div>
  <div class="abs about-mark">Fenwick<br>Painters</div>
</section>

<section class="abs services">
  <h2 class="section-title serif">Our Services</h2>
  <ul class="service-list">
    <li class="service-item"><div class="service-photo" role="img" aria-label="Painted two-storey house exterior with lawn" style="background:linear-gradient(180deg,#c9d6e6 0%,#d9d6cc 45%,#6f8f3c 100%)"></div><h3 class="serif">Exterior Painting</h3></li>
    <li class="service-item"><div class="service-photo" role="img" aria-label="Freshly painted empty interior room" style="background:linear-gradient(180deg,#d8d0c4 0%,#bfb3a3 55%,#6f5f52 100%)"></div><h3 class="serif">Interior Painting</h3></li>
    <li class="service-item"><div class="service-photo" role="img" aria-label="Patterned wallpaper on a feature wall" style="background:linear-gradient(90deg,#eef0ee 0%,#8e9892 35%,#6f7a74 70%,#dfe3e1 100%)"></div><h3 class="serif">Wallpapering</h3></li>
    <li class="service-item"><div class="service-photo" role="img" aria-label="Painted grey roof and weatherboard gable" style="background:linear-gradient(180deg,#dfe8f2 0%,#9aa4b0 40%,#c9ccd2 100%)"></div><h3 class="serif">Roof Painting</h3></li>
  </ul>
  <div class="abs btn btn-dark services-btn">View More<span class="arrow"><svg width="16" height="16" viewBox="0 0 16 16"><circle cx="8" cy="8" r="8" fill="#151b29"/><path d="M4 8h7M8 5l3 3-3 3" stroke="#fff" stroke-width="1.8" fill="none"/></svg></span></div>
</section>

<section class="abs gallery">
  <h2 class="section-title serif">Our Gallery</h2>
  <div class="g" role="img" aria-label="Grey weatherboard house with brown deck" style="left:110px;top:161px;width:346px;height:267px;background:linear-gradient(180deg,#3f7fd6 0%,#c8ccd3 45%,#7ba24a 100%)"></div>
  <div class="g" role="img" aria-label="Modern kitchen interior" style="left:110px;top:435px;width:171px;height:165px;background:linear-gradient(180deg,#d9d6d1,#8d7460)"></div>
  <div class="g" role="img" aria-label="Dark roof over a porch" style="left:285px;top:435px;width:171px;height:165px;background:linear-gradient(180deg,#9fb2c9 0%,#56585e 50%,#d4d2cc 100%)"></div>
  <div class="g" role="img" aria-label="Two-storey beige house with gardens" style="left:465px;top:161px;width:353px;height:439px;background:linear-gradient(180deg,#5b8fd4 0%,#c2b393 45%,#b7a37c 70%,#4f7a34 100%)"></div>
  <div class="g" role="img" aria-label="Bright living room with blue sofa" style="left:825px;top:161px;width:265px;height:218px;background:linear-gradient(180deg,#eef0ef,#c7cdd6 60%,#2e3f62)"></div>
  <div class="g" role="img" aria-label="Pale blue weatherboard cottage" style="left:825px;top:386px;width:265px;height:214px;background:linear-gradient(180deg,#aac0d8 0%,#c9d2de 45%,#5f8a3b 100%)"></div>
  <svg class="gallery-arrow" style="left:50px" width="18" height="26" viewBox="0 0 18 26"><path d="M14 3 4 13l10 10" stroke="#111" stroke-width="3.5" fill="none"/></svg>
  <svg class="gallery-arrow" style="left:1131px" width="18" height="26" viewBox="0 0 18 26"><path d="M4 3l10 10L4 23" stroke="#111" stroke-width="3.5" fill="none"/></svg>
</section>

<section class="abs testimonials">
  <h2 class="section-title serif">Our Testimonials</h2>
  <article class="quote-card" style="left:101px"><div class="quote-mark">&#8220;</div><p>We chose Rowan and his team to complete painting work around our home. Rowan is very knowledgeable, careful and thorough. We felt we could trust him to do an excellent job in a timely manner. His prices are reasonable and communication throughout has been excellent.</p></article>
  <article class="quote-card" style="left:442px"><div class="quote-mark">&#8220;</div><p>hese guys are great from beginning to end. Very professional, excellent business-men, hard workers, and top-quality work. Excellent communication, do what they say they will do and more, and really go the extra mile to make the job as painless as possible. Without reservations</p></article>
  <article class="quote-card" style="left:783px"><div class="quote-mark">&#8220;</div><p>If anyone is looking for a painter, I can highly recommend Fenwick Painters &amp; Decorators.Rowan has just finished repainting the inside of our home and we have been very impressed with his workmanship, attention to detail, communication and respect for our family.</p></article>
  <div class="author" style="left:142px"><div class="avatar" role="img" aria-label="Customer portrait"></div><div><h4 class="serif">Maren (June, 2018)</h4><div class="stars">★★★★★</div></div></div>
  <div class="author" style="left:483px"><div class="avatar" role="img" aria-label="Customer portrait"></div><div><h4 class="serif">Clara Hensley (2020)</h4><div class="stars">★★★★★</div></div></div>
  <div class="author" style="left:824px"><div class="avatar" role="img" aria-label="Customer portrait"></div><div><h4 class="serif">Delia (June, 2018)</h4><div class="stars">★★★★★</div></div></div>
  <div class="dots"><span></span><span class="on"></span><span></span></div>
</section>

<svg class="abs footer-shape" width="1200" height="514" viewBox="0 0 1200 514">
  <path d="M0 185 C260 -40 940 -40 1200 195 L1200 514 L0 514 Z" fill="#151b29"/>
</svg>

<footer>
  <div class="footer-col" style="left:115px"><h5>Quick Links</h5><ul><li>Home</li><li>Services</li><li>Gallery</li><li>About Us</li><li>All Testimonials</li><li>Contact</li></ul></div>
  <div class="footer-col" style="left:303px"><h5>Other Links</h5><ul><li>FAQ</li><li>Services</li><li>Team</li><li>Privacy</li><li>Policy</li></ul></div>
  <div class="footer-col" style="left:485px;width:290px"><h5>Mailing List</h5>
    <p>Sign up for our mailing list to get latest updates and offers.</p>
    <div class="mail-form"><div class="mail-input">Email address</div><div class="mail-btn"><svg width="14" height="12" viewBox="0 0 14 12"><path d="M1 6l4 4 8-9" stroke="#fff" stroke-width="2.4" fill="none"/></svg></div></div>
    <p class="privacy">We respect your privacy</p>
    <div class="socials"><span></span><span></span><span class="on"></span><span></span><span></span></div>
  </div>
  <div class="footer-col" style="left:852px;width:240px"><h5>About Us</h5>
    <p style="font-size:14px;line-height:25px">We strive &nbsp;ensure the highest quality paint-work, paying close attention to detail to provide a long lastingfinish.</p>
    <div class="contact-row" style="margin-top:6px"><svg width="14" height="14" viewBox="0 0 14 14"><path d="M3 1l3 3-2 2a8 8 0 0 0 4 4l2-2 3 3-2 2C6 13 1 8 1 3z" fill="#fff"/></svg>021 555 0148</div>
    <div class="contact-row" style="margin-top:14px"><svg width="14" height="11" viewBox="0 0 14 11"><rect width="14" height="11" fill="#fff"/><path d="M0 0l7 6 7-6" stroke="#151b29" stroke-width="1.5" fill="none"/></svg>hello@fenwickpainters.example</div>
    <div class="contact-row"><svg width="12" height="16" viewBox="0 0 12 16"><path d="M6 0a6 6 0 0 1 6 6c0 4-6 10-6 10S0 10 0 6a6 6 0 0 1 6-6z" fill="#fff"/><circle cx="6" cy="6" r="2.2" fill="#151b29"/></svg>Harrowfield, Kestrel Bay.</div>
  </div>
  <div class="abs footer-rule"></div>
  <div class="abs partners"><div class="partner-name"><i></i>Velmora</div><div class="partner-badge" role="img" aria-label="Accredited painter badge"></div></div>
  <div class="abs copyright">©Copyrights 2022 &nbsp;Fenwick Painter &nbsp;All Rights Reserved.</div>
</footer>

</body>
</html>
```